Website Home Page for Women's Health Medical Office

Redesign existing homepage for website using existing logo. Current website location is www.meadowcrestwomens.com. Please give it a modern, streamlined, playful feel.

Please give it a feminine feel and make it bright and cheerful using logo colors.

Target Market(s)

Women between the ages of 25-45

Industry/Entity Type

Medical Office

Coding

Coded - Design and coding required

Number of Pages Required

1 page

Font styles to use
Sans Serif
Other font styles liked:
• SEGOI UI script for text and GIL SANS for bold (or their equivilent)

Colors
E54698
E96AAD
F1A4CE
F9D9EA
FCEFF6

Requirements
Must have
• Existing logo. Logo Colors. Feminine, cheerful, simple design. all relevant contact information
Nice to have
• clean lines and streamlined look
Should not have
• Cluttered

```html
<!DOCTYPE html>
<html lang="en">
<head>
<meta charset="utf-8">
<title>Meadowcrest OB/GYN — Fairhaven, CA</title>
<link href="https://fonts.googleapis.com/css2?family=Open+Sans:wght@400;600;700&family=Lato:wght@400;700&display=swap" rel="stylesheet">
<style>
:root{
  --pink:#e54698;
  --pink-mid:#e96aad;
  --pink-soft:#f1a4ce;
  --pink-pale:#f9d9ea;
  --pink-mist:#fceff6;
  --plum:#6a2a78;
  --ink:#333333;
  --dark:#3a3a3a;
  --grey:#ebebeb;
  --muted:#777777;
  --navy:#1f2a4a;
  --white:#ffffff;
}
*{box-sizing:border-box;margin:0;padding:0}
html,body{width:1200px;height:3684px;overflow:hidden}
body{position:relative;background:var(--white);font-family:"Open Sans",sans-serif;color:var(--ink)}
.abs{position:absolute}
.topbar{top:0;left:0;width:1200px;height:42px;border-bottom:1px solid #e3e3e3;font-size:13px;color:var(--navy)}
.topbar .social{left:98px;top:10px;display:flex;gap:16px}
.topbar .social span{width:22px;height:22px;border:2px solid var(--navy);border-radius:50%;display:block}
.contact{top:12px;display:flex;align-items:center;gap:6px;white-space:nowrap}
.contact svg{width:13px;height:13px;flex:none}
.sep{top:11px;width:1px;height:20px;background:#999}
.brand{display:flex;align-items:center;gap:8px;font-weight:700;color:var(--pink);white-space:nowrap}
.brand i{display:block;border-radius:50%;background:var(--pink-pale);border:2px solid var(--pink);flex:none}
.header .brand{left:100px;top:78px;font-size:15px;gap:6px}
.header .brand i{width:28px;height:28px}
.nav{top:82px;left:335px;display:flex;gap:40px;font-size:17px;color:var(--navy);font-weight:600;letter-spacing:.3px;white-space:nowrap}
.btn{display:inline-block;background:var(--pink);color:var(--white);border-radius:5px;text-align:center;font-weight:600}
.book{left:967px;top:67px;width:133px;height:45px;line-height:45px;font-size:17px}
.hero-art{left:560px;top:150px;width:640px;height:640px;border-radius:48% 40% 20% 60%;background:radial-gradient(circle at 60% 40%,var(--plum),#9b4a8c 45%,var(--pink-soft) 75%,rgba(249,217,234,0) 90%)}
.leaf-wash{left:0;top:140px;width:360px;height:300px;background:radial-gradient(ellipse at 20% 30%,var(--pink-pale),rgba(252,239,246,0) 70%)}
.welcome{left:98px;top:272px;font-size:38px;color:var(--pink-mid);font-family:Lato,sans-serif}
.hero-title{left:98px;top:320px;font-size:66px;line-height:75px;font-weight:700;color:var(--ink);white-space:nowrap}
.start{left:105px;top:494px;width:191px;height:55px;line-height:55px;font-size:22px}
.founder-photo{left:98px;top:936px;width:407px;height:534px;background:linear-gradient(160deg,#6b7380,#3c4450 60%,#1d2a44)}
.founder-tag{left:505px;top:945px;width:60px;height:525px;writing-mode:vertical-rl;font-family:Georgia,serif;font-size:58px;font-weight:700;color:var(--pink-pale);letter-spacing:2px;white-space:nowrap}
.rule{height:3px;width:58px;background:var(--pink)}
.serve-rule{left:648px;top:978px}
.serve-title{left:645px;top:998px;font-size:35px;line-height:43px;font-weight:700;color:#111;white-space:nowrap}
.serve-copy{left:645px;top:1115px;width:455px;font-size:14.5px;line-height:25.7px;color:var(--muted);font-family:Lato,sans-serif}
.serve-btn{left:649px;top:1363px;width:178px;height:55px;line-height:55px;font-size:21px}
.help-band{left:0;top:1510px;width:1200px;height:780px}
.help-rule{left:566px;top:1635px;width:68px}
.help-title{left:0;top:1655px;width:1200px;text-align:center;font-size:34px;font-weight:700;color:var(--ink)}
.card{top:1740px;width:238px;height:445px;border-radius:119px;background:var(--dark);color:var(--white);text-align:center}
.card.alt{background:var(--pink)}
.card .pic{margin:12px auto 0;width:204px;height:204px;border-radius:50%}
.card h3{margin-top:26px;font-size:19px;font-weight:700;white-space:nowrap}
.card p{margin:14px auto 0;width:200px;font-size:12.3px;line-height:25.7px}
.card .more{margin:18px auto 0;width:128px;height:38px;line-height:38px;border-radius:5px;background:var(--pink);font-size:15px;font-weight:600}
.card.alt .more{background:var(--white);color:var(--pink)}
.spec-circle{left:93px;top:2455px;width:515px;height:515px;border-radius:50%;background:linear-gradient(180deg,#5a5a5a 0%,var(--dark) 25%);color:var(--white);text-align:center}
.spec-circle h2{margin-top:80px;font-size:34px;line-height:42px;font-weight:700}
.spec-circle p{margin:18px auto 0;width:400px;font-size:14.5px;line-height:22px}
.spec-circle p+p{margin-top:16px}
.spec-circle em{font-style:normal;color:var(--pink);font-weight:600}
.spec-btn{display:block;margin:36px auto 0;width:128px;height:38px;line-height:38px;background:var(--white);color:var(--pink);border-radius:5px;font-size:15px;font-weight:600}
.spec-frame{left:651px;top:2432px;width:427px;height:555px;border:2px solid var(--white)}
.spec-photo{left:668px;top:2413px;width:432px;height:557px;background:linear-gradient(160deg,#a9b7b0,#7e9aa7 40%,#d9a38e 75%,#8a6a5e)}
.footer-brand{left:0;top:3190px;width:1200px;justify-content:center;font-size:26px}
.footer-brand i{width:52px;height:52px}
.accept{left:0;top:3308px;width:1200px;text-align:center;font-size:35px;font-weight:700;color:var(--ink)}
.signup{left:193px;top:3382px;width:814px;height:60px;border:1px solid #cfcfcf;border-radius:30px}
.submit{left:856px;top:3387px;width:145px;height:50px;line-height:50px;border-radius:25px;background:var(--pink);color:var(--white);text-align:center;font-weight:700;font-size:16px}
.foot-nav{left:0;top:3476px;width:1200px;display:flex;justify-content:center;gap:36px;font-size:17px;color:var(--navy);white-space:nowrap}
.foot-social{left:0;top:3550px;width:1200px;display:flex;justify-content:center;gap:26px}
.foot-social span{width:22px;height:22px;border-radius:50%;background:var(--navy);display:block}
.foot-social span:nth-child(2){background:none;border:2px solid var(--pink)}
.copy{left:0;top:3622px;width:1200px;text-align:center;font-size:19px;color:var(--ink)}
</style>
</head>
<body>

<div class="abs topbar">
  <div class="abs social"><span></span><span></span><span></span></div>
  <div class="abs contact" style="left:290px">
    <svg viewBox="0 0 16 16"><rect x="1" y="3" width="14" height="10" fill="none" stroke="#1f2a4a" stroke-width="1.6"/><path d="M1 3l7 6 7-6" fill="none" stroke="#1f2a4a" stroke-width="1.6"/></svg>hello@meadowcrestwomens.com</div>
  <div class="abs sep" style="left:520px"></div>
  <div class="abs contact" style="left:540px">
    <svg viewBox="0 0 16 16"><rect x="1" y="3" width="14" height="10" fill="none" stroke="#1f2a4a" stroke-width="1.6"/><path d="M1 3l7 6 7-6" fill="none" stroke="#1f2a4a" stroke-width="1.6"/></svg>1840 Linden Grove Road, Suite 300, Fairhaven, CA 92410</div>
  <div class="abs sep" style="left:948px"></div>
  <div class="abs contact" style="left:966px">
    <svg viewBox="0 0 16 16"><path d="M4 1l3 4-2 2c1 2 2 3 4 4l2-2 4 3-2 3C7 15 1 9 1 4z" fill="#1f2a4a"/></svg>+ 555- 014-2290</div>
</div>

<header class="header">
  <div class="abs brand"><i></i>Meadowcrest OB/GYN</div>
  <nav class="abs nav"><span>HOME</span><span>SERVICES</span><span>RESOURCES</span><span>ABOUT US</span><span>CONTACT US</span></nav>
  <span class="abs btn book">Book Now</span>
</header>

<section class="hero">
  <div class="abs leaf-wash"></div>
  <div class="abs hero-art" role="img" aria-label="Illustration of an expectant mother with long flowing hair among pink leaves"></div>
  <svg class="abs" style="left:0;top:740px" width="1200" height="180" viewBox="0 0 1200 180">
    <path d="M0 160C150 40 500 30 1200 20" fill="none" stroke="var(--pink)" stroke-width="5"/>
    <path d="M100 50C400 25 800 15 1200 10" fill="none" stroke="var(--pink-soft)" stroke-width="3"/>
  </svg>
  <div class="abs welcome">WELCOME TO</div>
  <h1 class="abs hero-title">MEADOWCREST OB/GYN,<br>FAIRHAVEN, CA</h1>
  <span class="abs btn start">Get Started</span>
</section>

<section class="founder">
  <div class="abs founder-photo" role="img" aria-label="Portrait of the practice founder in navy scrubs"></div>
  <div class="abs founder-tag">OUR FOUNDER</div>
  <div class="abs rule serve-rule"></div>
  <h2 class="abs serve-title">SERVING WILLOW SPRINGS<br>MEDICAL CENTER</h2>
  <p class="abs serve-copy">At Meadowcrest OB/GYN in Fairhaven, California, we believe better health starts when the patient is educated. For this reason, we take time to listen to our patients concerns, explain each option available, and to answer any questions our patients may have so that they can make informed decisions. At Meadowcrest OB/GYN, our providers tailor every procedure performed and treatment option recommended to meet the specific needs of our patients. We remain up-to-date on the latest technology and practice</p>
  <span class="abs btn serve-btn">Read More</span>
</section>

<section class="help">
  <svg class="abs help-band" viewBox="0 0 1200 780" preserveAspectRatio="none">
    <path d="M0 220C200 80 600 60 1200 0V720C900 680 400 700 0 710Z" fill="var(--grey)"/>
    <path d="M0 225C200 85 600 65 1200 2" fill="none" stroke="var(--pink)" stroke-width="6"/>
  </svg>
  <div class="abs rule help-rule"></div>
  <h2 class="abs help-title">HOW CAN WE HELP YOU?</h2>
  <div class="abs card" style="left:100px">
    <div class="pic" role="img" aria-label="Photo of a smiling pregnant woman" style="background:linear-gradient(160deg,#eef0f2,#c9ccd3)"></div>
    <h3>PREGNANCY CARE</h3>
    <p>Receiving regular care in pregnancy is important for the health of both you and your baby.</p>
    <div class="more">Read More</div>
  </div>
  <div class="abs card alt" style="left:355px">
    <div class="pic" role="img" aria-label="Photo of a woman holding a birth control pill pack" style="background:linear-gradient(160deg,#fafafa,#d8cfc9)"></div>
    <h3>BIRTH CONTROL</h3>
    <p>Our gynecologists are knowledgeable on all forms of birth control including</p>
    <div class="more">Read More</div>
  </div>
  <div class="abs card" style="left:609px">
    <div class="pic" role="img" aria-label="Photo of a young woman reading a thermometer" style="background:linear-gradient(160deg,#f4f4f4,#b7a9b0)"></div>
    <h3>WELL WOMAN EXAMS</h3>
    <p>Our providers will help you to stay healthy by performing a physical exam on you annually.</p>
    <div class="more">Read More</div>
  </div>
  <div class="abs card" style="left:862px">
    <div class="pic" role="img" aria-label="Photo of a woman smiling at a desk" style="background:linear-gradient(160deg,#cfd6d0,#8e9a96)"></div>
    <h3>WOMEN'S HEALTH</h3>
    <p>Whether you are dealing with painful or irregular periods, fibroids, or other women's health i</p>
    <div class="more">Read More</div>
  </div>
</section>

<section class="specialists">
  <svg class="abs" style="left:0;top:2200px" width="1200" height="950" viewBox="0 0 1200 950">
    <path d="M0 0C300 120 700 130 1200 80V880C800 900 300 860 0 760Z" fill="var(--pink-soft)"/>
    <path d="M0 10C300 130 700 140 1200 90" fill="none" stroke="var(--pink)" stroke-width="6"/>
    <path d="M0 700C300 880 800 900 1200 900" fill="none" stroke="var(--pink)" stroke-width="10"/>
    <path d="M0 760C350 920 800 930 1200 940" fill="none" stroke="var(--pink-mid)" stroke-width="5"/>
  </svg>
  <div class="abs spec-circle">
    <h2>YOUR OB/GYN<br>SPECIALISTS</h2>
    <p>Meadowcrest OB/GYN offers you the best care possible in a personalized setting. We are currently accepting patients. Call our office now to make an appointment.</p>
    <p>Meadowcrest OB/GYN (located near Willow Springs Hospital in Fairhaven, CA) is a medical office that specializes in Christ-centered healthcare for women of all ages. <em>Our team of exclusively female providers</em> have years of experience taking care of women with a variety of pregnancy and gynecology concerns.</p>
    <span class="spec-btn">Read More</span>
  </div>
  <div class="abs spec-frame"></div>
  <div class="abs spec-photo" role="img" aria-label="Photo of a provider in scrubs holding a newborn baby"></div>
</section>

<footer>
  <div class="abs brand footer-brand"><i></i>Meadowcrest OB/GYN</div>
  <h2 class="abs accept">NOW ACCEPTING NEW PATIENTS</h2>
  <div class="abs signup"></div>
  <div class="abs submit">SUBMIT</div>
  <nav class="abs foot-nav"><span>HOME</span><span>ABOUT US</span><span>NEWS</span><span>PATIENT RESOURCES</span><span>PRIVACY POLICY</span><span>CONTACT US</span></nav>
  <div class="abs foot-social"><span></span><span></span><span></span><span></span></div>
  <p class="abs copy">© copyrights 2022 Meadowcrest |&nbsp; All Rights Reserved</p>
</footer>

</body>
</html>
```